Boutique custom software development company needs new business card

Our nearly 20 year old custom software development company would like to better include the fact that we are now providing Bitcoin services. These new services are B2B include education (how to acquire and securely hold Bitcoin) and integrating Bitcoin payments into existing ecommerce sites or other existing systems. Please keep the card clean and simple. Attached is our current design and some other files. vextorial.com

Target Market(s)

businesses owners interested in long term relationship

Industry/Entity Type

Custom software development and Bitcoin

Contact Information for Business Card

Dale Parker, dale@vextorial.com, vextorial.com, (888) 555-VXTRL

Font styles to use
Other font styles liked:
• monospace

Requirements
Must have
• double-sided
Nice to have
• clean and simple
Should not have
• physical address

```html
<!DOCTYPE html>
<html lang="en">
<head>
<meta charset="utf-8">
<title>Vextorial Business Card</title>
<link rel="stylesheet" href="https://fonts.googleapis.com/css2?family=Poppins:wght@300;400;500;600;700&display=swap">
<style>
  :root {
    --backdrop: #1b1b1b;
    --paper: #ffffff;
    --brand-orange: #f07b22;
    --brand-blue: #3a6fb7;
    --ink: #3a3a3a;
    --rule: #c9d6ea;
    --shadow: rgba(0,0,0,0.85);
  }
  html, body {
    margin: 0;
    padding: 0;
    width: 1075px;
    height: 1200px;
    overflow: hidden;
    background: var(--backdrop);
    font-family: "Poppins", sans-serif;
  }
  .canvas {
    position: relative;
    width: 1075px;
    height: 1200px;
  }
  .card {
    position: absolute;
    border-radius: 27px;
    box-shadow: 3px 3px 0 var(--shadow);
    overflow: hidden;
  }
  .card--front {
    left: 209px; top: 188px; width: 659px; height: 393px;
    background: var(--paper);
  }
  .card--back {
    left: 206px; top: 637px; width: 663px; height: 393px;
    background: var(--brand-orange);
    display: flex; flex-direction: column; align-items: center; justify-content: center;
  }
  .brand {
    position: absolute;
    left: 40px; top: 150px; width: 262px;
    text-align: center;
  }
  .brand__name {
    font-weight: 700;
    font-size: 44px;
    line-height: 1;
    color: var(--brand-blue);
    letter-spacing: -0.5px;
  }
  .brand__tagline {
    margin-top: 10px;
    font-weight: 300;
    font-size: 16px;
    color: var(--brand-blue);
    letter-spacing: -0.4px;
    white-space: nowrap;
  }
  .divider {
    position: absolute;
    left: 329px; top: 118px;
    width: 1px; height: 157px;
    background: var(--rule);
  }
  .contact {
    position: absolute;
    left: 366px; top: 116px;
  }
  .contact__name {
    margin: 0 0 34px;
    font-weight: 700;
    font-size: 27px;
    line-height: 1.1;
    letter-spacing: -0.3px;
  }
  .contact__first { color: var(--brand-orange); }
  .contact__last { color: var(--brand-blue); }
  .contact__list { list-style: none; margin: 0; padding: 0; }
  .contact__item {
    display: flex; align-items: center;
    height: 29.5px;
    font-size: 20px;
    color: var(--ink);
    white-space: nowrap;
  }
  .contact__icon {
    width: 25px; height: 25px;
    margin-right: 9px;
    flex: none;
  }
  .contact__highlight { color: var(--brand-blue); }
  .back__name {
    font-weight: 700;
    font-size: 70px;
    color: var(--paper);
    letter-spacing: -1px;
    line-height: 1;
    margin-top: 6px;
  }
  .back__services {
    margin-top: 16px;
    font-weight: 500;
    font-size: 17px;
    color: var(--paper);
    letter-spacing: 2px;
    text-transform: uppercase;
  }
</style>
</head>
<body>
<div class="canvas">
  <section class="card card--front">
    <div class="brand">
      <div class="brand__name">VEXTORIAL</div>
      <div class="brand__tagline">developer of custom applications</div>
    </div>
    <div class="divider"></div>
    <div class="contact">
      <h1 class="contact__name"><span class="contact__first">DALE</span> <span class="contact__last">PARKER</span></h1>
      <ul class="contact__list">
        <li class="contact__item">
          <svg class="contact__icon" viewBox="0 0 25 25" aria-hidden="true">
            <rect width="25" height="25" rx="3" fill="var(--brand-orange)"/>
            <path d="M8 6.5c-1 .6-1.5 1.6-1.2 2.8.9 3.5 3.5 6.2 7 7.2 1.2.3 2.2-.2 2.8-1.2l-2.2-1.8-1.3 1c-1.6-.8-2.9-2.1-3.7-3.7l1-1.3z" fill="#fff"/>
            <path d="M14 7.5a4 4 0 0 1 3.5 3.5M14 5a6.5 6.5 0 0 1 6 6" stroke="#fff" stroke-width="1.3" fill="none" stroke-linecap="round"/>
          </svg>
          (888) 555-VXTRL
        </li>
        <li class="contact__item">
          <svg class="contact__icon" viewBox="0 0 25 25" aria-hidden="true">
            <rect width="25" height="25" rx="3" fill="var(--brand-orange)"/>
            <rect x="5" y="7.5" width="15" height="10" fill="none" stroke="#fff" stroke-width="1.4"/>
            <path d="M5 7.5l7.5 6 7.5-6" fill="none" stroke="#fff" stroke-width="1.4"/>
          </svg>
          dale@vextorial.com
        </li>
        <li class="contact__item">
          <svg class="contact__icon" viewBox="0 0 25 25" aria-hidden="true">
            <rect width="25" height="25" rx="3" fill="var(--brand-orange)"/>
            <g fill="none" stroke="#fff" stroke-width="1.2">
              <circle cx="12.5" cy="12.5" r="6.5"/>
              <ellipse cx="12.5" cy="12.5" rx="3" ry="6.5"/>
              <path d="M6 12.5h13M7 9h11M7 16h11"/>
            </g>
          </svg>
          www.<span class="contact__highlight">vextorial</span>.com
        </li>
      </ul>
    </div>
  </section>

  <section class="card card--back">
    <div class="back__name">VEXTORIAL</div>
    <div class="back__services">Custom Software &middot; Bitcoin Services</div>
  </section>
</div>
</body>
</html>
```